University Student Business Card

Looking for a professional university student business card. Student is studying business with a focus on marketing. Some combination using a monogram and/or full name on the front with full name, university details and contact information on the back. Card should be modern design for a young professional. Prefer use of royal blue, black and white but am open to other uses of colour palette if it reinforces young/trendy style. Initials for a monogram are: KR. Full details will be provided in private consultation with designer(s).

Target Market(s)

Professional business people, marketers, advertisers, consultants

Industry/Entity Type

Business, marketing

Contact Information for Business Card

Monogram or personal logo, full name, university name, program of study, phone number, email address, pathfolio address

Other font styles liked:
• Open to suggestion to fulfill above requirements

Colors
0054AA
0677BA
7BADD7
CADEEF
E8F1F8

Requirements
Must have
• Monogram using letters K and R, and incorporate the business card details listed in the brief (specific details including personal contact info will be shared with successful designer to ensure privacy)
Nice to have
• Personal brand using monogram or personal logo (not a business logo)

```html
<!DOCTYPE html>
<html lang="en">
<head>
<meta charset="utf-8">
<title>KR Student Business Card</title>
<link href="https://fonts.googleapis.com/css2?family=Montserrat:wght@400;500;600&display=swap" rel="stylesheet">
<style>
  :root {
    --royal: #0054AA;
    --royal-mid: #0677BA;
    --white: #ffffff;
    --paper: #f4f4f4;
    --ink: #222222;
    --stage: #1f1f1f;
    --rule-light: #cfd6de;
    --rule-dark: rgba(255,255,255,0.45);
  }
  * { box-sizing: border-box; margin: 0; padding: 0; }
  html, body {
    width: 1200px; height: 900px; overflow: hidden;
    background: var(--stage);
    font-family: "Montserrat", Arial, sans-serif;
  }
  .sheet {
    width: 1200px; height: 900px;
    display: flex; flex-direction: column;
    align-items: center; justify-content: center; gap: 60px;
  }
  .card {
    width: 560px; height: 320px;
    display: flex; flex-direction: column;
    align-items: center; justify-content: center;
    text-align: center;
  }
  .card--front { background: var(--paper); color: var(--royal); }
  .card--back { background: var(--royal); color: var(--white); }

  .monogram {
    font-size: 96px; font-weight: 600; line-height: 1;
    color: var(--royal); letter-spacing: 2px;
    margin-bottom: 22px;
  }
  .holder-name {
    font-size: 22px; font-weight: 500; letter-spacing: 0.5px;
    text-transform: uppercase; color: var(--royal);
  }
  .holder-role {
    font-size: 14px; font-weight: 400; color: var(--ink);
    margin-top: 2px;
  }
  .rule {
    width: 110px; height: 1px; margin: 14px 0;
    background: var(--rule-light);
  }
  .card--back .rule { background: var(--rule-dark); }
  .profile-link {
    display: flex; align-items: center; gap: 8px;
    font-size: 14px; color: var(--ink);
  }
  .profile-dot {
    width: 20px; height: 20px; border-radius: 50%;
    background: var(--royal-mid);
  }

  .university-name {
    font-size: 26px; font-weight: 600; letter-spacing: 0.5px;
    text-transform: uppercase;
  }
  .contact-block {
    font-size: 15px; line-height: 1.4; font-weight: 400;
  }
</style>
</head>
<body>
<main class="sheet">
  <section class="card card--front" aria-label="Card front">
    <div class="monogram">KR</div>
    <h1 class="holder-name">Daniel Hart</h1>
    <p class="holder-role">Business Marketing</p>
    <div class="rule"></div>
    <p class="profile-link"><span class="profile-dot"></span>pathfolio.com/name</p>
  </section>

  <section class="card card--back" aria-label="Card back">
    <h2 class="university-name">University Name</h2>
    <div class="rule"></div>
    <p class="contact-block">217, Harbor Crescent Avenue<br>30418, Westland</p>
    <div class="rule"></div>
    <p class="contact-block">061-482 390 517<br>hello@kroffice.net<br>www.krstudiohub.net</p>
  </section>
</main>
</body>
</html>
```